Need Web Design for Business Process Outsourcing Company (Quorvane)

Quorvane is a business process outsourcing company. Need a simple site similar to http://www.tallowbrinkhire.com/ but with a more professional and credible look. New to the process; not sure where to start and comparing my options. Please let me know what my options are if I choose to go with you. Logo is attached for your reference. Please use same colorway

Reason: I want the final product to be coded. Please confirm you will be able to code final design.

Industry/Entity Type

Business

Coding

Coded - Design and coding required

```html
<!DOCTYPE html>
<html lang="en">
<head>
<meta charset="utf-8">
<title>Quorvane — Business Process Outsourcing</title>
<link rel="stylesheet" href="https://fonts.googleapis.com/css2?family=Mulish:wght@300;400;600;700;800&display=swap">
<style>
:root{
  --blue:#0a86c8;
  --blue-dark:#0d4e8c;
  --navy:#0b3f73;
  --navy-deep:#083462;
  --ink:#2f3a45;
  --muted:#7a8088;
  --light:#f2f2f2;
  --grey:#e6e6e6;
  --white:#ffffff;
}
*{box-sizing:border-box;margin:0;padding:0}
html,body{width:1200px;height:2609px;overflow:hidden}
body{position:relative;font-family:"Mulish",Arial,sans-serif;color:var(--ink);background:var(--white)}
.abs{position:absolute}
a{color:inherit;text-decoration:none}

/* top bar */
.topbar{left:0;top:0;width:1200px;height:35px;background:var(--blue-dark);color:#dbe8f5;font-size:11px}
.topbar .item{position:absolute;top:11px;display:flex;align-items:center;gap:10px;white-space:nowrap}
.topbar svg{width:12px;height:12px}

/* hero */
.hero{left:0;top:35px;width:1200px;height:680px;overflow:hidden}
.hero-photo{position:absolute;inset:0;background:
  radial-gradient(ellipse 340px 420px at 900px 300px,#f1d8c8 0%,#e7cbb9 35%,rgba(230,220,215,0) 70%),
  linear-gradient(100deg,#c9d6e2 0%,#b7c4d0 30%,#d9e1e8 55%,#eef1f4 100%)}
.logo{left:165px;top:55px;display:flex;align-items:center;gap:10px}
.logo .mark{width:44px;height:44px;background:var(--blue-dark)}
.logo .name{font-size:34px;font-weight:700;color:var(--blue-dark);letter-spacing:-.5px}
.nav{left:468px;top:66px;display:flex;font-size:11px;color:#33404c;white-space:nowrap}
.nav a{display:block;height:35px;line-height:35px;padding:0 13px;text-transform:uppercase;white-space:nowrap}
.nav a.active{background:var(--blue);color:var(--white);padding:0 16px;position:relative}
.nav a.active::after{content:"";position:absolute;left:50%;margin-left:-6px;bottom:-6px;border:6px solid transparent;border-bottom:0;border-top-color:var(--blue)}
.hero-box{left:170px;top:235px;width:486px;height:252px;background:rgba(255,255,255,.35);padding:30px 30px}
.hero-box h1{font-size:42px;font-weight:400;color:var(--blue-dark);line-height:1}
.hero-box h1 b{font-weight:800}
.hero-box p{margin-top:20px;font-size:12px;line-height:22px;color:#2c3640;font-weight:600}
.btn{display:inline-block;background:var(--blue);color:var(--white);font-size:13px;font-weight:700;text-align:center;white-space:nowrap}
.hero-box .btn{margin-top:18px;width:120px;height:36px;line-height:36px}
.slider-arrow{width:24px;height:24px;border:1.5px solid var(--blue-dark);border-radius:50%;top:498px}
.slider-arrow svg{width:100%;height:100%}
.wave{left:0;top:520px;width:1200px;height:200px}

/* welcome */
.mission{left:165px;top:630px;width:205px;height:257px}
.mission-photo{position:absolute;left:30px;top:52px;width:175px;height:205px;border-radius:50%;background:radial-gradient(circle at 50% 60%,#8b8a84,#b9bcbd 55%,#d7dcdf)}
.mission-small{position:absolute;left:0;top:0;width:120px;height:120px;border-radius:50%;border:4px solid var(--white);background:radial-gradient(circle at 40% 50%,#4c6f95,#6f8fa9 60%,#a8b6c0)}
.mission-label{position:absolute;left:60px;top:168px;font-size:24px;font-weight:700;color:rgba(255,255,255,.8)}
.section-rule{width:22px;height:3px;background:var(--blue)}
.welcome{left:393px;top:690px;width:320px}
.welcome h2{margin-top:14px;font-size:20px;font-weight:400;color:var(--blue-dark);white-space:nowrap}
.welcome h2 b{font-weight:800}
.welcome p{margin-top:16px;font-size:11.5px;line-height:22.5px;color:var(--muted)}
.welcome .btn{margin-top:14px;width:120px;height:35px;line-height:35px}

.quote{left:742px;top:675px;width:295px;height:339px;background:linear-gradient(180deg,#0f5fa3,#0b4580);padding:26px 30px}
.quote h3{font-size:20px;font-weight:400;color:var(--white);margin-left:-2px}
.quote .field{margin-top:10px;height:30px;background:var(--white);font-size:9px;color:#777;padding:8px 8px}
.quote .field:first-of-type{margin-top:24px}
.quote .field.area{height:52px}
.quote .btn{display:block;margin:14px auto 0;width:120px;height:34px;line-height:34px;font-size:13px}

/* services */
.services{left:0;top:1070px;width:1200px;height:478px;background:var(--light)}
.center-head{text-align:center}
.center-head .section-rule{margin:0 auto}
.center-head h2{margin-top:16px;font-size:21px;font-weight:400;color:var(--blue)}
.center-head h2 b{font-weight:800}
.service{position:absolute;top:106px;width:258px;height:278px;text-align:center;padding-top:28px}
.service h4{font-size:12px;font-weight:800;color:var(--blue-dark);text-transform:uppercase}
.service svg{display:block;margin:22px auto 0;width:46px;height:38px}
.service p{margin:22px auto 0;width:210px;font-size:9.5px;line-height:22px;color:#555}
.service.featured{background:var(--blue);border-top:5px solid var(--blue-dark);padding-top:23px}
.service.featured h4,.service.featured p{color:var(--white)}
.service.featured::after{content:"";position:absolute;left:121px;bottom:-8px;border:8px solid transparent;border-bottom:0;border-top-color:var(--blue)}
.dots{position:absolute;left:580px;top:429px;display:flex;gap:8px}
.dots i{display:block;width:7px;height:7px;border-radius:50%;background:var(--blue-dark)}

/* news */
.news{left:0;top:1548px;width:1200px;height:674px;background:var(--grey)}
.left-head h2{margin-top:10px;font-size:21px;font-weight:400;color:var(--blue-dark)}
.left-head h2 b{font-weight:800}
.news-photo{left:188px;top:94px;width:370px;height:214px;background:linear-gradient(180deg,#5d7fa1 0%,#8fa6bb 45%,#4a5864 75%,#2d3338 100%)}
.news-photo .btn{position:absolute;left:127px;top:88px;width:118px;height:34px;line-height:34px}
.news-body{left:595px;top:115px;width:418px}
.news-body h3{font-size:17px;font-weight:800;color:var(--blue-dark);padding-bottom:10px;border-bottom:1px solid #d3d3d3}
.news-body p{margin-top:12px;font-size:10.5px;line-height:23px;color:var(--muted)}
.news-body .date{margin-top:8px;font-size:10px;color:var(--blue-dark);display:inline-block;padding-bottom:3px;border-bottom:1px solid var(--blue)}
.presence{left:205px;top:395px;width:420px}
.presence h2{margin-top:10px;font-size:21px;font-weight:400;color:var(--blue)}
.presence h2 b{font-weight:800}
.presence p{margin-top:12px;font-size:10.5px;line-height:23px;color:var(--muted)}
.presence .btn{margin-top:16px;width:120px;height:35px;line-height:35px}
.world{left:656px;top:408px;width:362px;height:170px;background:radial-gradient(ellipse at 50% 50%,#c9d0d6,#d8dde1 60%,rgba(230,230,230,0) 100%)}
.map-logo{left:800px;top:594px;display:flex;align-items:center;gap:6px}
.map-logo .mark{width:22px;height:22px;background:var(--blue-dark)}
.map-logo .name{font-size:18px;font-weight:700;color:var(--blue-dark)}

/* partners */
.partners{left:0;top:2222px;width:1200px;height:94px;background:var(--white)}
.partner{position:absolute;top:32px;height:30px;background:#c7c9cc;border-radius:3px}

/* footer */
.footer{left:0;top:2316px;width:1200px;height:254px;background:radial-gradient(circle at 140px 150px,rgba(255,255,255,.08) 0 40px,transparent 41px),radial-gradient(circle at 620px 60px,rgba(255,255,255,.06) 0 60px,transparent 61px),linear-gradient(180deg,#1a5f99,#0f4e86);color:#d4e3f1}
.footer h5{font-size:16px;font-weight:400;color:var(--white)}
.fcol{position:absolute;top:36px}
.quick li{list-style:none;font-size:10.5px;line-height:22.5px;margin-top:0}
.quick ul{margin-top:14px}
.quick li::before{content:"::";margin-right:14px;color:#9fc1e0;font-size:9px}
.newsletter .email{margin-top:18px;width:150px;height:28px;background:var(--white);font-size:9px;color:#555;padding:8px 10px}
.newsletter .btn{margin-top:8px;width:98px;height:26px;line-height:26px;font-size:10px}
.contact p{font-size:10px;line-height:26px;color:var(--white);white-space:nowrap}
.contact .gap{margin-top:14px}
.contact .first{margin-top:12px}
.social{display:flex;gap:8px;margin-top:18px}
.social i{display:block;width:36px;height:36px;border:1px solid rgba(255,255,255,.35)}
.foot-logo{display:flex;align-items:center;gap:6px;margin-top:40px}
.foot-logo .mark{width:22px;height:22px;background:#c8d6e4}
.foot-logo .name{font-size:18px;font-weight:700;color:#c8d6e4}
.bottombar{left:0;top:2570px;width:1200px;height:39px;background:var(--navy-deep);color:#c9d8e7;font-size:8.5px;text-align:center;line-height:39px}
</style>
</head>
<body>

<div class="abs topbar">
  <div class="item" style="left:660px">
    <svg viewBox="0 0 24 24" fill="#dbe8f5"><path d="M6.6 10.8a15 15 0 0 0 6.6 6.6l2.2-2.2a1 1 0 0 1 1-.3 11 11 0 0 0 3.6.6 1 1 0 0 1 1 1V20a1 1 0 0 1-1 1A17 17 0 0 1 3 4a1 1 0 0 1 1-1h3.5a1 1 0 0 1 1 1c0 1.2.2 2.4.6 3.6a1 1 0 0 1-.3 1z"/></svg>
    <span style="margin-left:16px">Call Us : 1-800 555 0142</span>
  </div>
  <div class="item" style="left:862px">
    <svg viewBox="0 0 24 24" fill="none" stroke="#dbe8f5" stroke-width="2"><rect x="3" y="5" width="18" height="14"/><path d="M3 5l9 8 9-8"/></svg>
    <span style="margin-left:16px">Email : hello@quorvane-mail.com</span>
  </div>
</div>

<section class="abs hero">
  <div class="hero-photo" role="img" aria-label="Photo of a smiling customer support agent wearing a headset, with colleagues blurred behind"></div>
</section>

<div class="abs logo"><span class="mark"></span><span class="name">Quorvane</span></div>

<nav class="abs nav">
  <a class="active" href="#">Who we are</a>
  <a href="#">Our Solutions</a>
  <a href="#">Our Strategy</a>
  <a href="#">Security</a>
  <a href="#">News</a>
  <a href="#">Contact Us</a>
</nav>

<div class="abs hero-box">
  <h1><b>Quorvane</b> Services</h1>
  <p>Sed quia non numquam eius modi tempora incidunt ut labore et dolore magnam aliquam quaerat voluptatem. Ut enim ad minima veniam, quis nostrum exercitationem ullam corporis suscipit laboriosam</p>
  <a class="btn" href="#">Learn More</a>
</div>
<div class="abs slider-arrow" style="left:197px"><svg viewBox="0 0 24 24"><path d="M13.5 8l-4 4 4 4" fill="none" stroke="#0d4e8c" stroke-width="1.6"/></svg></div>
<div class="abs slider-arrow" style="left:227px"><svg viewBox="0 0 24 24"><path d="M10.5 8l4 4-4 4" fill="none" stroke="#0d4e8c" stroke-width="1.6"/></svg></div>

<svg class="abs wave" viewBox="0 0 1200 200" preserveAspectRatio="none">
  <path d="M0 22 C220 -10 420 20 620 90 C820 160 1000 170 1200 150 L1200 200 L0 200Z" fill="#c9dbe8"/>
  <path d="M0 20 C220 -6 420 28 620 100 C820 172 1000 186 1200 176 L1200 200 L0 200Z" fill="#ffffff"/>
</svg>

<div class="abs mission">
  <div class="mission-photo" role="img" aria-label="Photo of stacked smooth stones by the sea"></div>
  <div class="mission-small" role="img" aria-label="Photo of call centre staff at their desks"></div>
  <span class="mission-label">Mission</span>
</div>

<div class="abs welcome">
  <div class="section-rule"></div>
  <h2>Welcome To <b>Quorvane</b> Services</h2>
  <p>Sed quia non numquam eius modi tempora incidunt ut labore et dolore magnam aliquam quaerat voluptatem. Ut enim ad minima veniam, quis nostrum exercitationem ullam corporis suscipit laboriosam, nisi ut aliquid ex ea commodi consequatur? Quis autem vel eum iure reprehenderit qui in ea voluptate velit esse quam nihil molestiae consequatur, vel illum qui dolorem eum fugiat quo voluptas nulla pariatur</p>
  <a class="btn" href="#">Learn More</a>
</div>

<form class="abs quote">
  <h3>Get a FREE Quote</h3>
  <div class="field">Name</div>
  <div class="field">Email</div>
  <div class="field">Phone</div>
  <div class="field area">Message</div>
  <span class="btn">SUBMIT</span>
</form>

<section class="abs services">
  <div class="center-head" style="margin-top:20px">
    <div class="section-rule"></div>
    <h2><b>Our</b> Services</h2>
  </div>
  <div class="service" style="left:161px">
    <h4>IT Soutions</h4>
    <svg viewBox="0 0 46 38" fill="none" stroke="#0a86c8" stroke-width="2.4"><rect x="2" y="2" width="42" height="30"/><path d="M17 11l-6 6 6 6M29 11l6 6-6 6M25 9l-4 16"/><path d="M16 36h14"/></svg>
    <p>Nam libero tempore, cum soluta nobis est eligendi optio cumque nihil impedit quo minus id quod maxime placeat facere possimus, omnis voluptas assumenda est,</p>
  </div>
  <div class="service featured" style="left:471px">
    <h4>Customer Services</h4>
    <svg viewBox="0 0 46 38" fill="none" stroke="#ffffff" stroke-width="2.6"><path d="M10 22v-5a13 13 0 0 1 26 0v5"/><rect x="7" y="19" width="6" height="10" fill="#fff"/><rect x="33" y="19" width="6" height="10" fill="#fff"/><path d="M36 29c0 5-5 7-11 7"/></svg>
    <p>Nam libero tempore, cum soluta nobis est eligendi optio cumque nihil impedit quo minus id quod maxime placeat facere possimus, omnis voluptas assumenda est,</p>
  </div>
  <div class="service" style="left:781px">
    <h4>Human Resources</h4>
    <svg viewBox="0 0 46 38" fill="#0a86c8"><circle cx="17" cy="10" r="7"/><circle cx="30" cy="11" r="6"/><path d="M4 36c0-9 6-14 13-14s13 5 13 14z"/><path d="M31 20c7 0 12 5 12 16h-10c0-7-2-12-6-15z"/></svg>
    <p>Nam libero tempore, cum soluta nobis est eligendi optio cumque nihil impedit quo minus id quod maxime placeat facere possimus, omnis voluptas assumenda est,</p>
  </div>
  <div class="dots"><i></i><i></i><i></i></div>
</section>

<section class="abs news">
  <div class="abs left-head" style="left:191px;top:46px">
    <div class="section-rule"></div>
    <h2><b>Latest</b> News</h2>
  </div>
  <div class="abs news-photo" role="img" aria-label="Photo of a businessman looking over a city skyline beneath a world map overlay">
    <a class="btn" href="#">Learn More</a>
  </div>
  <div class="abs news-body">
    <h3>Finibus Bonorum et Malorum</h3>
    <p>Nor again is there anyone who loves or pursues or desires to obtain pain of itself, because it is pain, but because occasionally circumstances occur in which toil and pain can procure him some great pleasure. To take a trivial example, which of us ever undertakes laborious physical exercise,</p>
    <span class="date">Nov- 12 -2016</span>
  </div>

  <div class="abs presence">
    <div class="section-rule"></div>
    <h2><b>Global Solutions</b> Presence</h2>
    <p>Nor again is there anyone who loves or pursues or desires to obtain pain of itself, because it is pain, but because occasionally circumstances occur in which toil and pain can procure him some great pleasure. To take a trivial example, which of us ever undertakes laborious physical exercise,</p>
    <a class="btn" href="#">Learn More</a>
  </div>
  <div class="abs world" role="img" aria-label="Dotted world map with office location pins"></div>
  <div class="abs map-logo"><span class="mark"></span><span class="name">Quorvane</span></div>
</section>

<section class="abs partners" aria-label="Partner badges">
  <span class="partner" style="left:190px;width:110px"></span>
  <span class="partner" style="left:334px;width:114px"></span>
  <span class="partner" style="left:496px;width:94px;top:26px;height:42px"></span>
  <span class="partner" style="left:635px;width:112px"></span>
  <span class="partner" style="left:785px;width:80px;top:26px;height:40px"></span>
  <span class="partner" style="left:906px;width:102px"></span>
</section>

<footer class="abs footer">
  <div class="fcol quick" style="left:200px">
    <h5>Quick Links</h5>
    <ul>
      <li>Who we are ?</li>
      <li>Our Solutions</li>
      <li>Our Strategy</li>
      <li>Security</li>
      <li>News</li>
      <li>Contact Us</li>
    </ul>
  </div>
  <div class="fcol newsletter" style="left:403px">
    <h5>Newsletter</h5>
    <div class="email">Enter Email id</div>
    <span class="btn">SUBSCRIBE</span>
  </div>
  <div class="fcol contact" style="left:642px">
    <h5>Contact Us</h5>
    <p class="first">Phone : 1-800 555 0199</p>
    <p>Email : hello@quorvane-mail.com</p>
    <p class="gap">Address : Quorvane</p>
    <p>Level 14, 88 Harbour Lane</p>
    <p>Sydney NSW 2000</p>
  </div>
  <div class="fcol" style="left:843px">
    <h5>Follow Us</h5>
    <div class="social"><i></i><i></i><i></i><i></i></div>
    <div class="foot-logo"><span class="mark"></span><span class="name">Quorvane</span></div>
  </div>
</footer>
<div class="abs bottombar">© 2016 .www.quorvane-site.com &nbsp;|&nbsp; All Rights Reserved.</div>

</body>
</html>
```